Advertising company unique advertising platform

we need a logo design for a new company based in Australia Melbourne. We develop innovated advertising platform where consumer can use this platform to get regular discount, as business owner they can use this platform for free advertisement. Payment for this advertisement platform only payable every two weeks, when I generate revenue for their business

Industry/Entity Type

Advertising

Contact Information for Business Card

Dale Morven | Co-Founder |Managing Director
Suite 718 240 Wattlebrook Lane Melbourne Vic 3000

ABN 38 614 207 923
Tel: +61 0487 259 318 | Email: dale.morven@plivorantu.com

Font styles to use
Decorative
Script

Requirements
Must have
• Try few different design and some round corner business card
Should not have
• One round corner business card...try 4 different colour background not only black, make sure two side is designed. Be creative so imagine you are giving this to a client make sure has wow factor, if you can also try one design with engrave like all the logo, words look 3d feel
• The word Advertising Platform use attached file font

```html
<!DOCTYPE html>
<html lang="en">
<head>
<meta charset="utf-8">
<title>Brightway Hub – Business Card</title>
<link rel="stylesheet" href="https://fonts.googleapis.com/css2?family=Roboto:ital,wght@0,400;0,500;1,700&display=swap">
<style>
  :root {
    --page: #2b2b2d;
    --card-black: #1b1b1c;
    --card-black-soft: #262627;
    --ink-light: #f1f1f1;
    --accent-red: #e8452c;
    --accent-teal: #2fe2b4;
    --grad-yellow: #f5c042;
    --grad-orange: #f07a2a;
    --grad-red: #e4472c;
    --logo-dark: #141414;
  }
  * { box-sizing: border-box; margin: 0; padding: 0; }
  html, body { width: 1200px; height: 886px; overflow: hidden; }
  body {
    background: var(--page);
    font-family: "Roboto", Arial, sans-serif;
    display: flex;
    flex-direction: column;
    align-items: center;
    justify-content: center;
    gap: 40px;
  }
  .card {
    position: relative;
    width: 640px;
    height: 366px;
    border-radius: 22px;
    overflow: hidden;
    background: linear-gradient(160deg, var(--card-black-soft), var(--card-black));
    box-shadow: 0 14px 30px rgba(0,0,0,.45);
  }

  /* Back side */
  .card-back {
    display: flex;
    flex-direction: column;
    align-items: center;
    justify-content: center;
    gap: 70px;
  }
  .brand-mark {
    display: flex;
    align-items: center;
    gap: 16px;
  }
  .brand-dot {
    width: 54px; height: 54px;
    border-radius: 50%;
    background: var(--grad-orange);
  }
  .brand-name {
    font-weight: 500;
    font-size: 44px;
    color: var(--grad-orange);
    letter-spacing: 1px;
  }
  .website {
    color: var(--ink-light);
    font-size: 15px;
    letter-spacing: 6px;
  }

  /* Front side */
  .front-art { position: absolute; inset: 0; }
  .details {
    position: absolute;
    left: 36px; top: 36px;
    color: var(--ink-light);
    font-size: 15px;
    line-height: 1.3;
  }
  .person-name {
    color: var(--accent-red);
    font-weight: 700;
    font-style: italic;
    font-size: 21px;
    text-transform: uppercase;
    letter-spacing: .3px;
  }
  .person-role {
    color: var(--accent-teal);
    font-weight: 700;
    font-style: italic;
    font-size: 15px;
    text-transform: uppercase;
    margin-bottom: 8px;
  }
  .block { margin-bottom: 8px; }
  .contact-line { display: flex; align-items: center; gap: 8px; }
  .contact-line svg { flex: none; }
  .front-brand {
    position: absolute;
    right: 40px; top: 70px;
    display: flex;
    align-items: center;
    gap: 10px;
  }
  .front-brand .brand-dot { width: 34px; height: 34px; background: var(--logo-dark); }
  .front-brand .brand-name { font-size: 27px; color: var(--logo-dark); }
</style>
</head>
<body>

  <section class="card card-back" aria-label="Card back">
    <div class="brand-mark">
      <span class="brand-dot"></span>
      <span class="brand-name">Brightway Hub</span>
    </div>
    <p class="website">www.plivorantu.com</p>
  </section>

  <section class="card card-front" aria-label="Card front">
    <svg class="front-art" viewBox="0 0 640 366" width="640" height="366" aria-hidden="true">
      <defs>
        <linearGradient id="warm" x1="0" y1="0" x2="1" y2="0.4">
          <stop offset="0" stop-color="var(--grad-yellow)"/>
          <stop offset="0.55" stop-color="var(--grad-orange)"/>
          <stop offset="1" stop-color="var(--grad-red)"/>
        </linearGradient>
      </defs>
      <path d="M398 0 C352 20 345 80 378 150 C410 225 390 320 330 366 L640 366 L640 0 Z" fill="var(--accent-teal)"/>
      <path d="M420 0 C372 22 368 85 398 152 C430 228 408 322 352 366 L640 366 L640 0 Z" fill="url(#warm)"/>
    </svg>

    <div class="details">
      <h1 class="person-name">Dale Morven</h1>
      <p class="person-role">Co-Founder<br>Managing Director</p>
      <p class="block">Plivo Rantu<br>ABN 38 614 207 923</p>
      <p class="block">Suite 718 240 Wattlebrook Lane<br>Melbourne Vic 3000</p>
      <p class="contact-line">
        <svg width="12" height="12" viewBox="0 0 24 24" aria-hidden="true"><path fill="var(--accent-red)" d="M6.6 10.8a15 15 0 0 0 6.6 6.6l2.2-2.2a1 1 0 0 1 1-.25 11.4 11.4 0 0 0 3.6.6 1 1 0 0 1 1 1V20a1 1 0 0 1-1 1A17 17 0 0 1 3 4a1 1 0 0 1 1-1h3.5a1 1 0 0 1 1 1c0 1.25.2 2.45.6 3.6a1 1 0 0 1-.25 1z"/></svg>
        +61 0487 259 318
      </p>
      <p class="contact-line">
        <svg width="12" height="12" viewBox="0 0 24 24" aria-hidden="true"><path fill="var(--accent-red)" d="M2 5h20v14H2z"/><path fill="none" stroke="var(--card-black)" stroke-width="2" d="M2 5l10 8 10-8"/></svg>
        dale.morven@plivorantu.com
      </p>
    </div>

    <div class="front-brand">
      <span class="brand-dot"></span>
      <span class="brand-name">Brightway Hub</span>
    </div>
  </section>

</body>
</html>
```